Flyer for the Lumen 2025 Conference

I am looking to produce a flyer for our upcoming conference, Lumen 2025. This is an annual conference that we plan to publicize on social media. The ideal designer will create a flyer that is eye-catching and effectively communicates the key information. Please see attached our logo, speaker photo, and flyer content.

Target Market(s)

All demographics

Industry/Entity Type

Christian

Font styles to use
Sans Serif

Requirements
Should not have
• Cross, church

```html
<!DOCTYPE html>
<html lang="en">
<head>
<meta charset="utf-8">
<title>Lumen 2025 Conference Flyer</title>
<link rel="stylesheet" href="https://fonts.googleapis.com/css2?family=Oswald:wght@300;400;700&family=Barlow+Condensed:wght@500;700;800&family=Barlow:wght@400;500&display=swap">
<style>
  :root{
    --stage:#7fa8ec;
    --paper:#e9e9eb;
    --navy:#063a66;
    --navy-deep:#031c33;
    --ink:#0a0f18;
    --orange:#f26a12;
    --gold:#c9b27a;
    --text:#2a3340;
    --silver-1:#f7f7f8;
    --silver-2:#b9bcc2;
  }
  *{box-sizing:border-box;margin:0;padding:0}
  html,body{width:1200px;height:900px;overflow:hidden}
  body{background:var(--stage);font-family:"Barlow",sans-serif;position:relative}
  .flyer{position:absolute;left:300px;top:30px;width:600px;height:840px;background:var(--paper);overflow:hidden;box-shadow:0 20px 40px rgba(10,30,80,.3)}
  .flyer__backdrop{position:absolute;inset:0}
  .speaker-photo{position:absolute;left:70px;top:110px;width:280px;height:440px;border-radius:0 0 120px 30px;
    background:linear-gradient(160deg,#1f6fc2 0%,#1457a3 45%,#0b2c56 100%)}
  .brand{position:absolute;left:30px;top:25px;width:96px;height:96px;background:var(--navy);border:1px solid #3d6e98;display:flex;align-items:center;justify-content:center}
  .brand__name{font-family:"Barlow",sans-serif;font-weight:500;color:#fff;font-size:17px;letter-spacing:1px}
  .headline{position:absolute;right:40px;top:100px;text-align:right;font-family:"Oswald",sans-serif;font-weight:300;color:var(--orange);line-height:1}
  .headline__main{font-size:52px;display:block}
  .headline__sub{font-size:34px;display:block;margin-top:4px}
  .topic-label{position:absolute;right:60px;top:240px;font-family:"Barlow Condensed",sans-serif;font-weight:800;font-style:italic;font-size:32px;letter-spacing:12px;color:var(--navy)}
  .topic-title{position:absolute;right:35px;top:278px;text-align:right;font-family:"Barlow Condensed",sans-serif;font-weight:800;color:var(--navy);line-height:.88;
    -webkit-text-stroke:2px var(--gold);text-shadow:3px 4px 0 rgba(0,0,0,.18)}
  .topic-title__word{display:block;font-size:124px;letter-spacing:2px}
  .topic-title__year{display:block;font-size:112px}
  .speaker-banner{position:absolute;left:40px;top:505px;width:320px;height:88px;border-radius:40px 0 40px 0;
    background:linear-gradient(100deg,#fff 0%,#f1f1f3 60%,#c9ccd2 100%);box-shadow:0 6px 14px rgba(0,0,0,.25);padding:12px 0 0 30px}
  .speaker-banner__label{font-family:"Barlow Condensed",sans-serif;font-weight:700;font-size:18px;letter-spacing:14px;color:var(--navy);padding-left:40px}
  .speaker-banner__name{font-family:"Barlow Condensed",sans-serif;font-weight:800;font-size:30px;color:var(--navy);margin-top:2px}
  .silver-lines{position:absolute;left:0;bottom:0;width:600px;height:40px}
  .info{position:absolute;left:40px;top:618px;width:240px;font-family:"Barlow Condensed",sans-serif;color:var(--text)}
  .info__title{font-size:16px;font-weight:500;margin-left:22px}
  .info__row{display:flex;align-items:center;gap:8px;font-size:19px;font-weight:500;margin-top:4px;line-height:1.2}
  .icon{width:14px;height:14px;flex:none}
  .info__app{font-family:"Barlow",sans-serif;font-size:11px;color:var(--orange);margin-top:8px;line-height:1.2}
  .store-badges{display:flex;gap:8px;margin-top:5px}
  .store-badge{width:66px;height:20px;background:#000;border-radius:3px}
  .schedule{position:absolute;left:300px;top:630px;width:270px;font-family:"Barlow Condensed",sans-serif;color:var(--text)}
  .schedule__title{font-size:17px;font-weight:500;text-align:center;margin-bottom:6px}
  .schedule__row{display:flex;gap:8px;font-size:15px;font-weight:500;line-height:1.2;margin-top:4px}
  .schedule__row .icon{margin-top:2px}
</style>
</head>
<body>
<main class="flyer">
  <svg class="flyer__backdrop" viewBox="0 0 600 840" aria-hidden="true">
    <defs>
      <linearGradient id="shine" x1="0" x2="1">
        <stop offset="0" stop-color="#fff" stop-opacity="0"/>
        <stop offset=".5" stop-color="#fff" stop-opacity=".9"/>
        <stop offset="1" stop-color="#aeb2b9"/>
      </linearGradient>
    </defs>
    <path d="M0 0 H360 C340 180 380 380 350 580 L0 610 Z" fill="#0a0f18"/>
    <path d="M60 0 H360 C340 180 380 380 350 580 L120 595 C140 360 80 180 60 0 Z" fill="#063a66"/>
    <path d="M280 600 L600 680 V720 L240 630 Z" fill="url(#shine)" opacity=".7"/>
  </svg>

  <div class="speaker-photo" role="img" aria-label="Photo of the speaker seated, wearing a blue suit and glasses"></div>

  <div class="brand"><span class="brand__name">HALVORA</span></div>

  <h1 class="headline">
    <span class="headline__main">A PROPHETIC</span>
    <span class="headline__sub">CONFERENCE</span>
  </h1>

  <p class="topic-label">TOPIC</p>
  <h2 class="topic-title">
    <span class="topic-title__word">LUMEN</span>
    <span class="topic-title__year">2025</span>
  </h2>

  <div class="speaker-banner">
    <p class="speaker-banner__label">SPEAKER</p>
    <p class="speaker-banner__name">PROPHET DAVID MENSAH</p>
  </div>

  <svg class="silver-lines" viewBox="0 0 600 40" aria-hidden="true">
    <rect x="0" y="0" width="600" height="40" fill="#d9dadd"/>
    <path d="M180 10 H600" stroke="#f7f7f8" stroke-width="5"/>
    <path d="M220 21 H600" stroke="#b9bcc2" stroke-width="3"/>
    <path d="M260 31 H600" stroke="#f7f7f8" stroke-width="4"/>
  </svg>

  <section class="info">
    <p class="info__title">More Info:</p>
    <p class="info__row">
      <svg class="icon" viewBox="0 0 16 16"><path d="M3 1l3 3-2 2c1 2 3 4 5 5l2-2 3 3-2 3C7 14 2 9 1 3z" fill="#f26a12"/></svg>
      555 014 2290</p>
    <p class="info__row">
      <svg class="icon" viewBox="0 0 16 16"><rect x="1" y="3" width="14" height="10" fill="none" stroke="#f26a12" stroke-width="1.6"/><path d="M1 3l7 6 7-6" fill="none" stroke="#f26a12" stroke-width="1.6"/></svg>
      contact@halvora.org</p>
    <p class="info__row">
      <svg class="icon" viewBox="0 0 16 16"><circle cx="8" cy="8" r="6.5" fill="none" stroke="#f26a12" stroke-width="1.6"/><path d="M1.5 8h13M8 1.5v13" stroke="#f26a12" stroke-width="1.3"/></svg>
      www.halvora.org</p>
    <p class="info__app">Download the HALVORA App<br>to stay updated on the event</p>
    <div class="store-badges"><span class="store-badge"></span><span class="store-badge"></span></div>
  </section>

  <section class="schedule">
    <p class="schedule__title">Date / Time :</p>
    <p class="schedule__row">
      <svg class="icon" viewBox="0 0 16 16"><rect width="16" height="16" rx="3" fill="#f26a12"/><circle cx="8" cy="7" r="3" fill="none" stroke="#fff" stroke-width="1.5"/><path d="M8 10v4" stroke="#fff" stroke-width="1.5"/></svg>
      <span>The Riverside Performing Arts Center<br>318 Alder Lane<br>Millbrook, Maine 04199</span></p>
    <p class="schedule__row">
      <svg class="icon" viewBox="0 0 16 16"><rect width="16" height="16" rx="3" fill="#f26a12"/><rect x="3.5" y="4.5" width="9" height="8" fill="none" stroke="#fff" stroke-width="1.3"/><path d="M3.5 7h9" stroke="#fff" stroke-width="1.3"/></svg>
      <span>Friday December 26th</span></p>
    <p class="schedule__row">
      <svg class="icon" viewBox="0 0 16 16"><circle cx="8" cy="8" r="8" fill="#f26a12"/><circle cx="8" cy="8" r="4.5" fill="none" stroke="#fff" stroke-width="1.3"/><path d="M8 5.5V8h2" fill="none" stroke="#fff" stroke-width="1.3"/></svg>
      <span>6:30PM - 9:00PM</span></p>
  </section>
</main>
</body>
</html>
```